Local Chiropractoc needs Modern Website

This website needs to have an upscale look with a very modern feel.

This is for a home page psd layout and an interior page psd file so 2 files total

Below is the information and websites to reference

Add Logo that is attached.

Build a color scheme similar to this website image titled "chiro-1" using the golds, whites, blacks and browns from the color of the logo

I want to see a light background so it makes the images and logo stick out

Must Include these pages in a horizontal menu bar in this order:
Home, Why Fair Ridge?, How Chiropractic Helps, Ask the Doctor, Work Place Wellness, Request an Appointment, Blog, Contact Us

Please add the following social media logos to the top and footer of the website: Chatterly, Plexo+, Vidzio

Build a "classy looking" Make An Appointment Button into the header with the contact info below

Phone Number:
555-014-2297

Address:
4172 North Maple Blvd, Suite #7
Brookhaven, FL 32704

This website needs 4 rotating banners. Please reference a layout similar to this for the banners: http://hollowpinespine.com/. However design it nicer than this website

Below are the description for each banner

Rotating Banner #1
Use Image: Patients are Saying
Add a line of text: "What our Patients are Saying"

Rotating Banner #2
Use Image: Becoming a Patient
Add a line of text: "Interested in Becoming a Patient"

Rotating Banner #3
Use Image: Dinner with Doctor
Add a line of text: "Win A free Dinner with Dr. Hollins"

Rotating Banner #4
Use Image: Chatterly
Add a line of text: Follow us on Chatterly
Bullet point these 4 lines underneath the "Follow us on Chatterly" text:
- Cutting Edge Health News
- Healthy Recipes
- Newest Health Products
- Clinic Events

I'd like to see a free consultation box similar to the "chiro-1" image. Fields to include are: First Name, Last Name, Phone Number, Comments

For the body, please fill it with latin text. Please design a professional 2 column layout similar to the www.hollowpinespine.com website. (DO NOT COPY THIS WEBSITE, USE IT AS REFERENCE)

In the left column include in this order:
Video
Rate us on Plexo Button, Find us on Chatterly Button
Welcome Letter

In the right column include this:

Office Hours
Monday: 8:00-11:00, 2:00-5:00
Tuesday: 8:30-11:00, 2:00-5:30
Wednesday: 8:00-11:00, 2:00-5:00
Thursday: 10:00-12:00, 2:30-5:00
Friday: 8:00-10:00, 1:00-5:00
Saturday: Closed
Sunday: Closed

Patient Testimonials
Fill with a latin text testimonial. This spot will rotate different testimonials

For the footer please design something similar to the layout of this: http://www.tidewellhealer.com/

Also include in the Footer: Powered by Crestline Pixel Group

```html
<!DOCTYPE html>
<html lang="en">
<head>
<meta charset="utf-8">
<title>Fair Ridge Chiropractic</title>
<link href="https://fonts.googleapis.com/css2?family=Open+Sans:ital,wght@0,400;0,600;0,700;0,800;1,400;1,600&display=swap" rel="stylesheet">
<style>
:root{
  --gold:#b08d4a;
  --gold-light:#c6a566;
  --dark:#2b2b2b;
  --darker:#232323;
  --page:#efefef;
  --card:#ffffff;
  --text:#7a7a7a;
  --heading:#2f2f2f;
  --rule:#ececec;
}
*{margin:0;padding:0;box-sizing:border-box}
html,body{width:805px;height:1200px;overflow:hidden}
body{position:relative;background:var(--page);font-family:"Open Sans",Arial,sans-serif;color:var(--text)}
.abs{position:absolute}

/* header */
.brand{left:107px;top:36px;display:flex;align-items:center;gap:8px}
.brand-mark{width:14px;height:64px;background:var(--dark)}
.brand-name{font-weight:800;font-size:22px;line-height:24px;color:var(--dark);letter-spacing:-.5px}
.brand-sub{font-weight:700;font-size:11.5px;line-height:14px;letter-spacing:1.6px;color:var(--dark)}
.social-top{left:652px;top:50px;display:flex;gap:3px}
.social-dot{width:18px;height:18px;border:1px solid var(--gold);border-radius:50%;font-size:7px;font-weight:700;color:var(--gold);display:flex;align-items:center;justify-content:center}
.social-dot.active{background:var(--gold);color:#fff}
.contact-bar{left:347px;top:79px;width:364px;height:30px;display:flex;background:var(--dark);color:#fff}
.contact-item{display:flex;align-items:center;gap:7px;padding:0 8px;font-size:6.5px;line-height:8.5px;border-right:1px solid #3f3f3f;white-space:nowrap}
.contact-item b{font-weight:700}
.contact-item span{color:#8f8f8f;font-style:italic}
.contact-item:first-child{width:95px}
.contact-item:nth-child(2){width:160px}
.appt-btn{flex:1;background:var(--gold);display:flex;align-items:center;justify-content:center;font-size:6.8px;font-weight:700;letter-spacing:.3px;clip-path:polygon(8px 0,100% 0,100% 100%,0 100%)}

/* nav */
.main-nav{left:93px;top:121px;width:619px;height:40px;background:var(--dark);display:flex;padding-left:11px}
.main-nav a{color:#e6e6e6;text-decoration:none;font-size:6.5px;display:flex;align-items:center;padding:0 10px;border-right:1px solid #3b3b3b;white-space:nowrap}
.main-nav a:last-child{border:none}
.main-nav a.current{background:var(--gold);color:#fff}

/* hero */
.hero{left:93px;top:171px;width:619px;height:202px;overflow:hidden}
.hero-copy{left:452px;top:36px;width:150px;color:#fff}
.hero-title{font-size:13px;font-weight:700;line-height:18px}
.hero-text{font-size:6.3px;line-height:13px;margin-top:8px;width:148px;text-align:justify}
.hero-btn{display:inline-block;margin-top:11px;background:#fff;color:var(--dark);font-size:6.3px;padding:6px 10px;border-radius:2px}
.hero-dots{display:flex;gap:3px}
.hero-dots i{width:6px;height:6px;border-radius:50%;background:#cdb58a}
.hero-dots i.on{background:#fff}

/* card */
.content-card{left:93px;top:382px;width:619px;height:717px;background:var(--card);border:1px solid #e4e4e4}
.section-title{display:flex;align-items:center;gap:6px;font-size:8.4px;font-weight:700;color:var(--heading);white-space:nowrap}
.section-title::before{content:"";width:2px;height:8px;background:var(--gold)}
.section-title::after{content:"";flex:1;height:5px;background:var(--rule)}
.video-frame{left:108px;top:435px;width:387px;height:201px;border:1px solid #e2e2e2;padding:5px}
.video-still{width:375px;height:170px;background:linear-gradient(160deg,#aeb7a4,#c9c4ae 45%,#8f9a6d);display:flex;align-items:center;justify-content:center}
.play{width:24px;height:22px;background:rgba(255,255,255,.5);display:flex;align-items:center;justify-content:center}
.video-controls{height:19px;background:var(--dark);display:flex;align-items:center;gap:6px;padding:0 6px;font-size:5.5px;color:#777}
.track{flex:1;height:3px;background:#555;position:relative}
.track::before{content:"";position:absolute;left:0;top:0;width:29%;height:3px;background:var(--gold)}
.track::after{content:"";position:absolute;left:29%;top:-2px;width:6px;height:6px;border-radius:50%;background:#fff}
.body-copy{font-size:6.6px;line-height:15.2px;color:var(--text);text-align:justify}
.welcome-photo{left:309px;top:677px;width:186px;height:165px;background:linear-gradient(150deg,#9bb07a,#d8c2a8 50%,#8aa0b4)}

/* sidebar */
.consult{left:510px;top:413px;width:187px;height:230px;background:var(--dark);clip-path:polygon(0 0,100% 0,100% 90%,50% 100%,0 90%)}
.consult-head{position:absolute;left:0;top:0;width:187px;height:54px;background:var(--gold);color:#fff;text-align:center;padding-top:9px;clip-path:polygon(0 0,100% 0,100% 70%,50% 100%,0 70%)}
.consult-head small{font-size:7px;display:block}
.consult-head strong{font-size:10.5px;font-weight:700;letter-spacing:.3px}
.consult-tag{position:absolute;top:60px;width:100%;text-align:center;font-size:7px;font-style:italic;font-weight:600;color:#fff}
.field{position:absolute;left:10px;width:167px;height:16px;background:#fff;border-radius:2px;font-size:5.8px;color:#555;padding:4px 10px}
.field.accent{color:var(--gold)}
.submit-btn{position:absolute;left:10px;top:184px;width:52px;height:18px;background:var(--gold);color:#fff;font-size:6px;font-weight:600;display:flex;align-items:center;justify-content:center;border:1px solid #d3b77f}
.rate-btn{left:510px;width:187px;height:30px;display:flex;background:var(--dark);border-right:2px solid var(--gold)}
.rate-icon{width:31px;background:var(--gold);color:#fff;font-weight:700;font-size:11px;display:flex;align-items:center;justify-content:center}
.rate-text{flex:1;text-align:center;color:#fff;font-size:5.5px;font-weight:600;padding-top:4px;line-height:7px}
.rate-text b{display:block;color:var(--gold-light);font-size:13px;line-height:15px;font-weight:800}
.hours{left:510px;top:739px;width:187px;background:#fff;border:1px solid #e3e3e3}
.hours-head{height:24px;background:var(--gold);color:#fff;font-size:8px;font-weight:700;display:flex;align-items:center;justify-content:center}
.hours-row{display:flex;justify-content:space-between;height:18px;align-items:center;padding:0 9px;font-size:5.6px;border-top:1px solid #e8e8e8;white-space:nowrap}
.hours-row:nth-child(odd){background:#f3f3f3}
.hours-row b{font-weight:700;color:#333}
.hours-row span{color:#999}
.hours-row.closed b,.hours-row.closed span{color:var(--gold)}
.testimonial{left:510px;top:932px;width:187px;height:138px;background:#f1f1f1;border:1px solid #e3e3e3}
.quote-mark{position:absolute;left:16px;top:2px;font-size:40px;font-weight:800;color:var(--gold);line-height:40px}
.quote-text{position:absolute;left:18px;top:15px;width:160px;font-size:6.3px;font-style:italic;line-height:13px;color:#999;text-align:justify;text-indent:26px}
.quote-foot{position:absolute;left:0;bottom:0;width:185px;height:21px;background:var(--gold);color:#fff;font-size:5.8px;font-weight:700;display:flex;align-items:center;justify-content:space-between;padding:0 14px}
.quote-foot i{display:inline-block;width:5px;height:5px;border-radius:50%;background:#d4bd92;margin-left:2px}
.quote-foot i.on{background:#fff}

/* footer */
.footer-links{left:0;top:1099px;width:805px;height:51px;background:var(--gold)}
.footer-nav{position:absolute;left:108px;top:20px;font-size:6.4px;color:#fff;word-spacing:1px;white-space:nowrap}
.footer-brand{position:absolute;left:637px;top:15px;color:#fff}
.footer-brand b{font-size:11px;font-weight:800;display:block;line-height:12px}
.footer-brand small{font-size:5.5px;font-weight:700;letter-spacing:.8px;display:block;line-height:8px}
.footer-base{left:0;top:1150px;width:805px;height:50px;background:var(--darker);color:#fff;font-size:6.2px}
.footer-addr{position:absolute;left:108px;top:16px;line-height:9px}
.footer-addr b{font-weight:700}
.footer-addr em{display:block;padding-left:24px}
.footer-social{position:absolute;left:367px;top:12px;display:flex;gap:6px}
.footer-social .social-dot{width:20px;height:20px;border-radius:2px}
.footer-copy{position:absolute;right:108px;top:16px;text-align:right;line-height:9px}
.footer-copy b{font-weight:700}
.footer-copy em span{color:var(--gold)}
</style>
</head>
<body>

<header>
  <div class="abs brand">
    <div class="brand-mark"></div>
    <div>
      <div class="brand-name">FAIR RIDGE</div>
      <div class="brand-sub">CHIROPRACTIC</div>
    </div>
  </div>
  <div class="abs social-top">
    <div class="social-dot">C</div>
    <div class="social-dot active">P+</div>
    <div class="social-dot">V</div>
  </div>
  <div class="abs contact-bar">
    <div class="contact-item">
      <svg width="13" height="13" viewBox="0 0 24 24"><path fill="#b08d4a" d="M6.6 10.8c1.4 2.8 3.8 5.1 6.6 6.6l2.2-2.2c.3-.3.7-.4 1-.2 1.1.4 2.3.6 3.6.6.6 0 1 .4 1 1V20c0 .6-.4 1-1 1C10.6 21 3 13.4 3 4c0-.6.4-1 1-1h3.5c.6 0 1 .4 1 1 0 1.3.2 2.5.6 3.6.1.3 0 .7-.2 1z"/></svg>
      <div><b>555-014-2297</b><br><span>info@example.com</span></div>
    </div>
    <div class="contact-item">
      <svg width="15" height="13" viewBox="0 0 24 22"><path fill="#b08d4a" d="M12 1 1 11h3v10h6v-6h4v6h6V11h3z"/></svg>
      <div><b>4172 North Maple Blvd, Suite #7</b><br><span>Brookhaven, FL 32704</span></div>
    </div>
    <div class="appt-btn">MAKE AN APPOINTMENT</div>
  </div>
</header>

<nav class="abs main-nav">
  <a href="#">HOME</a>
  <a href="#" class="current">WHY FAIR RIDGE?</a>
  <a href="#">HOW CHIROPRACTIC HELPS</a>
  <a href="#">ASK THE DOCTOR</a>
  <a href="#">WORK PLACE WELLNESS</a>
  <a href="#">REQUEST AN APPOINTMENT</a>
  <a href="#">BLOG</a>
  <a href="#">CONTACT US</a>
</nav>

<section class="abs hero">
  <svg width="619" height="202" viewBox="0 0 619 202">
    <defs>
      <linearGradient id="heroPhoto" x1="0" y1="0" x2="1" y2="1">
        <stop offset="0" stop-color="#6b5a3c"/>
        <stop offset=".45" stop-color="#b99a7c"/>
        <stop offset="1" stop-color="#3d5a8e"/>
      </linearGradient>
    </defs>
    <rect width="619" height="202" fill="url(#heroPhoto)" role="img" aria-label="Photo of the smiling clinic team"/>
    <path d="M412 0 C390 40 430 80 412 125 C398 160 405 185 428 202 L619 202 L619 0 Z" fill="#b08d4a"/>
    <path d="M412 0 C390 40 430 80 412 125 C398 160 405 185 428 202" fill="none" stroke="#fff" stroke-width="3"/>
  </svg>
  <div class="abs hero-copy">
    <div class="hero-title">Interested in<br>Becoming a Patient?</div>
    <p class="hero-text">Proin sit amet venenatis ante. Nulla lorem felis, maximus tincidunt felis nec, mattis con dimentum enim. Maecenas non sodales nund.</p>
    <span class="hero-btn">Read More</span>
  </div>
  <div class="abs hero-dots" style="left:452px;top:186px"><i></i><i class="on"></i><i></i><i></i></div>
</section>

<main class="abs content-card"></main>

<h2 class="abs section-title" style="left:108px;top:411px;width:387px">OUR VIDEOS</h2>
<div class="abs video-frame">
  <div class="video-still" role="img" aria-label="Video still of a smiling family outdoors">
    <div class="play"><svg width="8" height="9" viewBox="0 0 8 9"><path d="M0 0 8 4.5 0 9z" fill="#fff"/></svg></div>
  </div>
  <div class="video-controls">
    <svg width="6" height="7" viewBox="0 0 8 9"><path d="M0 0 8 4.5 0 9z" fill="#888"/></svg>
    <span>00:28</span><div class="track"></div><span>02:36</span>
  </div>
</div>

<h2 class="abs section-title" style="left:108px;top:655px;width:387px">WELCOME LETTER</h2>
<div class="abs body-copy" style="left:108px;top:673px;width:187px">Hello Dear Visitor,<br>Vestibulum malesuada tortor volutpat risus finibus, in con sequat nibh dictum. Pellen tesque vestibulum nisi nisl, vel accumsan dui consequat sed. Integer non justo et mi interd um pretium. Proin ut pulvinar eros. Pellentesque at luctus odio, a ullamcorper urna. Nam semper feugiat massa non pulvinar. Curabitur sagittis, odio eget posuere ultricies, sem nisi pulvinar turpis, at laoreet arcu neque lacinia odio. Nulla nec nunc ac felis auctor fermentum quis ut justo. Donec ultricies feugiat accumsan. Integer leo justo, dapi bus id mauris quis, vestibulum rutrum arcu.</div>
<div class="abs welcome-photo" role="img" aria-label="Photo of a happy family embracing"></div>
<p class="abs body-copy" style="left:108px;top:858px;width:387px">Vestibulum malesuada tortor volutpat risus finibus, in con sequat nibh dictum. Pellen tesque vestibulum nisi nisl, vel accumsan dui consequat sed. Integer non justo et mi interd um pretium. Proin ut pulvinar eros. Pellentesque at luctus odio, a ullamcorper urna. Nam semper feugiat massa non pulvinar. Curabitur sagittis, odio eget posuere ultricies, sem nisi pulvi nar turpis, at laoreet arcu neque lacinia odio. Nulla nec nunc ac felis auctor fermentum quis ut justo. Donec ultricies feugiat accumsan. Integer leo justo, dapi bus id mauris quis, vestibulum rutrum arcu. Donec diam magna, mattis ac odio id, dignis sim euismod eros. Proin id luctus dolor, vel imperdiet ante. Morbi rhoncus fringilla neque, non tristique ante interdum ac. Etiam lacinia neque sagittis, commodo diam at, ullamcorper urna.</p>
<p class="abs body-copy" style="left:108px;top:978px;width:387px">In sodales velit nec magna pellentesque, nec dignissim eros porta. Nam congue maximus elit. Quisque sapien nunc, lobortis et nulla eu, eleifend sodales velit. Aliquam aliquam eros lectus, facilisis dictum libero feugiat nec. Nunc quis elit pulvinar, aliquam ipsum in, lacinia enim. Fusce a consequat erat. Aliquam urna dui, malesuada in vehicula cursus, porttitor quis risus. Pellentesque tristique consectetur libero, et suscipit eros fringilla et. Morbi fringilla sapien sed elit lobortis, non cursus velit tincidunt.</p>

<aside class="abs consult">
  <div class="consult-head"><small>CONTACT US NOW &amp; GET YOUR</small><strong>FREE CONSULTATION</strong></div>
  <div class="consult-tag">WELLNESS BEGINS HERE</div>
  <div class="field" style="top:76px">First Name</div>
  <div class="field accent" style="top:96px">Last Name</div>
  <div class="field" style="top:118px">Phone Number</div>
  <div class="field" style="top:138px;height:40px">Comments ...</div>
  <div class="submit-btn">Submit &#9758;</div>
</aside>

<div class="abs rate-btn" style="top:653px"><div class="rate-icon">P+</div><div class="rate-text">RATE US ON<b>PLEXO</b></div></div>
<div class="abs rate-btn" style="top:688px"><div class="rate-icon">C</div><div class="rate-text">FIND US ON<b>CHATTERLY</b></div></div>

<div class="abs hours">
  <div class="hours-head">OFFICE HOURS</div>
  <div class="hours-row"><b>Monday</b><span>8:00-11:00 AM, 2:00-5:00 PM</span></div>
  <div class="hours-row"><b>Tuesday</b><span>8:30-11:00 AM, 2:00-5:30 PM</span></div>
  <div class="hours-row"><b>Wednesday</b><span>8:00-11:00 AM, 2:00-5:00 PM</span></div>
  <div class="hours-row"><b>Thursday</b><span>10:00-12:00 AM, 2:30-5:00 PM</span></div>
  <div class="hours-row"><b>Friday</b><span>8:00-10:00 AM, 1:00-5:00 PM</span></div>
  <div class="hours-row closed"><b>Saturday</b><span>Closed</span></div>
  <div class="hours-row closed"><b>Sunday</b><span>Closed</span></div>
</div>

<h2 class="abs section-title" style="left:510px;top:910px;width:187px">PATIENT TESTIMONIALS</h2>
<div class="abs testimonial">
  <div class="quote-mark">&ldquo;</div>
  <p class="quote-text">Pellentesque habitant morbi tristique senectus et netus et malesuada fames ac turpis egestas. Donec faucibus aliquet dui, nec congue orci sagittis eget. nteger leo justo, dapibus id mauris quis, vestibulum rutrum arcu. Etiam sed ipsum eu augue condimentum ullam corper vel ac sapien.</p>
  <div class="quote-foot"><span>- Mr. Daniel Forsythe -</span><span><i></i><i class="on"></i><i></i><i></i></span></div>
</div>

<footer>
  <div class="abs footer-links">
    <div class="footer-nav">Home &nbsp;|&nbsp; Why Fair Ridge? &nbsp;|&nbsp; How Chiropractic Helps &nbsp;|&nbsp; Ask the Doctor &nbsp;|&nbsp; Work Place Wellness &nbsp;|&nbsp; Request an Appointment &nbsp;|&nbsp; Blog &nbsp;|&nbsp; Contact Us</div>
    <div class="footer-brand"><b>FAIR RIDGE</b><small>CHIROPRACTIC</small></div>
  </div>
  <div class="abs footer-base">
    <div class="footer-addr"><b>4172 North Maple Blvd, Suite #7</b><em>Brookhaven, FL 32704</em></div>
    <div class="footer-social">
      <div class="social-dot">C</div>
      <div class="social-dot active">P+</div>
      <div class="social-dot">V</div>
    </div>
    <div class="footer-copy"><b>Copyright &copy; 2015, Fair Ridge Chiropractic</b><br><em>Powered by <span>Crestline Pixel Group</span></em></div>
  </div>
</footer>

</body>
</html>
```